Design a Website for an IT Support Company

We are an IT support company that provides commercial IT support and services to small and medium sized businesses. We are in need of a website to be developed for our business.
We would like to work with someone who is either familiar with the IT field, or has developed a website for an IT support company in the past.
Some examples of designs/layouts that we like:
https://www.veldaworks.example/
http://www.marsbyquill.example/
http://817kq.example/
http://www.olbenstructures.example/
http://www.bykq.example/
I have attached a word document that gives a menu system/page layout format that we would like for our website as well as branch office phone numbers. Our logo is also attached that you can use for your design purposes. We currently do not have copy produced for all of the pages outlined in the word document, but would get this done during the project with the selected designer.
We would like the website to be SEO friendly & fully responsive. We would prefer a Wordpress format, however, we are open to HTML formats as well.

```html
<!DOCTYPE html>
<html lang="en">
<head>
<meta charset="utf-8">
<title>Corvane IT</title>
<link rel="stylesheet" href="https://fonts.googleapis.com/css2?family=Roboto+Condensed:wght@400;700&family=Lato:wght@400;700&display=swap">
<style>
:root{
  --blue:#0b72c2;
  --blue-dark:#075a9c;
  --ink:#333;
  --muted:#666;
  --band:#ececec;
  --footer:#1b1b1b;
  --footer-text:#cfcfcf;
}
*{box-sizing:border-box;margin:0;padding:0}
html,body{width:842px;height:1200px;overflow:hidden;background:#fff}
body{position:relative;font-family:"Lato",sans-serif;color:var(--ink)}
.abs{position:absolute}

/* header */
.site-header{left:0;top:0;width:842px;height:82px;border-bottom:2px solid var(--blue)}
.brand{left:55px;top:30px;display:flex;align-items:center;gap:8px;font-family:"Lato",sans-serif;font-weight:700;font-size:24px;color:var(--ink)}
.brand-dot{width:18px;height:18px;border-radius:50%;background:var(--blue)}
.header-phone{right:54px;top:10px;display:flex;align-items:center;gap:6px;font-family:"Roboto Condensed",sans-serif;font-weight:700;font-size:22px;color:var(--blue)}
.main-nav{right:54px;top:42px;display:flex;gap:0;font-family:"Lato",sans-serif;font-size:12px;text-transform:uppercase}
.main-nav a{display:block;padding:0 10px;line-height:29px;color:#555;text-decoration:none}
.main-nav a.is-active{background:var(--blue);color:#fff;border-radius:3px;padding:0 14px;margin-right:10px}

/* hero */
.hero{left:0;top:83px;width:842px;height:392px;background:linear-gradient(90deg,#8d94a3 0%,#c9ccd2 30%,#e8e8e9 55%,#d7d9dc 80%,#b7bcc4 100%)}
.hero-title{right:55px;top:88px;text-align:right;font-family:"Lato",sans-serif;font-weight:700;font-size:40px;line-height:44px;color:#2e2e2e}
.hero-sub{right:55px;top:185px;width:360px;text-align:right;font-size:14px;line-height:20px;color:#333}
.hero-cta{right:55px;top:240px;width:146px;height:41px;line-height:41px;text-align:center;background:var(--blue);color:#fff;border-radius:4px;font-family:"Roboto Condensed",sans-serif;font-size:17px;box-shadow:0 8px 8px -6px rgba(0,0,0,.5)}
.slider-arrow{top:183px;width:40px;height:28px;background:rgba(255,255,255,.7);display:flex;align-items:center;justify-content:center}
.slider-arrow span{width:28px;height:20px;background:var(--blue);display:flex;align-items:center;justify-content:center}
.slider-arrow.prev{left:0}
.slider-arrow.next{right:0}

/* welcome */
.welcome{left:0;top:512px;width:842px;text-align:center}
.welcome h1{font-family:"Roboto Condensed",sans-serif;font-weight:400;font-size:31px;color:#555}
.welcome h1 em{font-style:normal;color:var(--blue)}
.welcome p{width:660px;margin:16px auto 0;font-size:10px;line-height:19px;color:var(--muted)}
.btn-more{display:inline-block;margin-top:16px;width:117px;height:36px;line-height:36px;background:var(--blue);color:#fff;border-radius:4px;font-family:"Roboto Condensed",sans-serif;font-size:16px;box-shadow:0 8px 8px -6px rgba(0,0,0,.5)}

/* services */
.services{left:0;top:715px;width:842px;height:220px;background:var(--band)}
.service-card{top:41px;width:175px;height:139px;background:#fff;border:1px solid #ddd;border-top:2px solid #999;text-align:center}
.service-card.is-active{border-top-color:var(--blue);box-shadow:0 2px 6px rgba(0,0,0,.2)}
.service-card svg{margin-top:22px}
.service-card h3{position:absolute;left:0;right:0;top:106px;font-family:"Roboto Condensed",sans-serif;font-weight:400;font-size:16px;color:#555}
.service-card.is-active h3{color:var(--blue)}

/* footer */
.site-footer{left:0;top:935px;width:842px;height:225px;background:var(--footer);border-top:2px solid var(--blue)}
.footer-col{top:24px}
.footer-col h4{font-family:"Roboto Condensed",sans-serif;font-weight:400;font-size:12px;color:var(--blue);width:145px;padding-bottom:8px;border-bottom:1px solid #3a3a3a;margin-bottom:12px}
.footer-col ul{list-style:none}
.link-list li{font-size:10px;color:var(--footer-text);line-height:23.5px;display:flex;align-items:center;gap:8px}
.link-list li::before{content:"";width:5px;height:5px;background:var(--blue)}
.contact-list li{font-size:10px;color:var(--footer-text);line-height:23.5px;display:flex;align-items:center;gap:8px}
.newsletter p{font-size:9.5px;line-height:16px;color:var(--footer-text);width:160px}
.newsletter .field{width:175px;height:25px;background:#fff;margin-top:6px;font-size:9.5px;color:#666;padding:0 10px;line-height:25px}
.newsletter .btn-sub{margin-top:8px;width:110px;height:29px;line-height:29px;text-align:center;background:var(--blue);color:#fff;border-radius:3px;font-family:"Roboto Condensed",sans-serif;font-size:15px}
.footer-brand{left:612px;top:102px;display:flex;align-items:center;gap:8px;font-weight:700;font-size:22px;color:#bbb}
.footer-brand .brand-dot{background:var(--blue)}
.social{left:638px;top:150px;display:flex;gap:14px}
.social span{width:30px;height:30px;border:2px solid var(--blue);border-radius:50%}
.copyright{left:0;top:1160px;width:842px;height:40px;background:var(--blue);color:#fff;font-size:10px;text-align:center;line-height:40px}
</style>
</head>
<body>

<header class="site-header abs">
  <div class="brand abs"><span class="brand-dot"></span>Corvane IT</div>
  <div class="header-phone abs">
    <svg width="24" height="24" viewBox="0 0 24 24"><circle cx="12" cy="12" r="11" fill="none" stroke="#0b72c2" stroke-width="1.5"/><path d="M8 6c1-1 2 0 3 2s0 2-1 3c1 2 2 3 3 4 1-1 1-2 3-1s3 2 2 3c-2 2-5 1-8-2s-4-7-2-9z" fill="#0b72c2"/></svg>
    555-014-2200
  </div>
  <nav class="main-nav abs">
    <a class="is-active" href="#">Home</a>
    <a href="#">About Us</a>
    <a href="#">Services</a>
    <a href="#">Why Corvane IT</a>
    <a href="#">Contact</a>
  </nav>
</header>

<section class="hero abs" role="img" aria-label="Photo of two colleagues working together at a laptop in a bright office"></section>
<h2 class="hero-title abs">GET MORE FROM<br>YOUR TECHNOLOGY</h2>
<p class="hero-sub abs">Provides Commercial It Support And Services To Small And Medium Sized Businesses</p>
<a class="hero-cta abs">CONTACT US</a>
<div class="slider-arrow prev abs"><span><svg width="10" height="12" viewBox="0 0 10 12"><path d="M7 1L2 6l5 5" fill="none" stroke="#fff" stroke-width="2"/></svg></span></div>
<div class="slider-arrow next abs"><span><svg width="10" height="12" viewBox="0 0 10 12"><path d="M3 1l5 5-5 5" fill="none" stroke="#fff" stroke-width="2"/></svg></span></div>

<section class="welcome abs">
  <h1>WELCOME TO <em>CORVANE IT</em></h1>
  <p>Lorem Ipsum is simply dummy text of the printing and typesetting industry. Lorem Ipsum has been the industry's standard dummy text ever since the 1500s, when an unknown printer took a galley of type and scrambled it to make a type specimen book. It has survived not only five centuries, but also the leap into electronic typesetting, remaining essentially unchanged.</p>
  <a class="btn-more">READ MORE</a>
</section>

<section class="services abs">
  <div class="service-card is-active abs" style="left:145px">
    <svg width="60" height="60" viewBox="0 0 60 60" fill="#aaa" stroke="#777" stroke-width="1"><g><ellipse cx="18" cy="22" rx="13" ry="4"/><rect x="5" y="22" width="26" height="8"/><rect x="5" y="30" width="26" height="8"/><rect x="5" y="38" width="26" height="8"/><ellipse cx="18" cy="46" rx="13" ry="4"/></g><g><ellipse cx="42" cy="12" rx="13" ry="4"/><rect x="29" y="12" width="26" height="8"/><rect x="29" y="20" width="26" height="8"/><rect x="29" y="28" width="26" height="8"/><ellipse cx="42" cy="36" rx="13" ry="4"/></g></svg>
    <h3>DATA</h3>
  </div>
  <div class="service-card abs" style="left:338px">
    <svg width="60" height="64" viewBox="0 0 60 64"><rect x="20" y="2" width="20" height="36" rx="10" fill="#999"/><path d="M12 28c0 12 8 18 18 18s18-6 18-18" fill="none" stroke="#777" stroke-width="4"/><rect x="28" y="46" width="4" height="10" fill="#777"/><rect x="20" y="56" width="20" height="4" fill="#777"/></svg>
    <h3>CLOUD</h3>
  </div>
  <div class="service-card abs" style="left:532px">
    <svg width="70" height="60" viewBox="0 0 70 60"><path d="M14 38a10 10 0 0 1 4-19 14 14 0 0 1 26-2 10 10 0 0 1 10 12 8 8 0 0 1-2 9z" fill="#fff" stroke="#999" stroke-width="3"/><rect x="22" y="36" width="44" height="14" rx="5" fill="#888"/><rect x="28" y="41" width="14" height="4" rx="2" fill="#ccc"/></svg>
    <h3>VOICE</h3>
  </div>
</section>

<footer class="site-footer abs">
  <div class="footer-col abs" style="left:55px">
    <h4>USEFUL LINKS</h4>
    <ul class="link-list">
      <li>Home</li><li>About Us</li><li>Services</li><li>Why Corvane IT</li><li>Contact Us</li>
    </ul>
  </div>
  <div class="footer-col abs" style="left:241px">
    <h4>CONTACT US</h4>
    <ul class="contact-list">
      <li><svg width="14" height="14" viewBox="0 0 24 24"><path d="M5 3c2-1 3 0 4 3s0 3-1 4c1 3 3 5 6 6 1-1 1-2 4-1s4 2 3 4c-3 3-7 2-11-2S2 6 5 3z" fill="#0b72c2"/></svg>Main Number : 555-014-2200</li>
      <li><svg width="14" height="14" viewBox="0 0 24 24"><path d="M5 3c2-1 3 0 4 3s0 3-1 4c1 3 3 5 6 6 1-1 1-2 4-1s4 2 3 4c-3 3-7 2-11-2S2 6 5 3z" fill="#0b72c2"/></svg>Houston: 555-016-3100</li>
      <li><svg width="14" height="14" viewBox="0 0 24 24"><path d="M5 3c2-1 3 0 4 3s0 3-1 4c1 3 3 5 6 6 1-1 1-2 4-1s4 2 3 4c-3 3-7 2-11-2S2 6 5 3z" fill="#0b72c2"/></svg>San Antonio : 555-018-4700</li>
      <li><svg width="14" height="14" viewBox="0 0 24 24"><path d="M5 3c2-1 3 0 4 3s0 3-1 4c1 3 3 5 6 6 1-1 1-2 4-1s4 2 3 4c-3 3-7 2-11-2S2 6 5 3z" fill="#0b72c2"/></svg>Austin : 555-012-9000</li>
      <li><svg width="14" height="14" viewBox="0 0 24 24"><path d="M5 3c2-1 3 0 4 3s0 3-1 4c1 3 3 5 6 6 1-1 1-2 4-1s4 2 3 4c-3 3-7 2-11-2S2 6 5 3z" fill="#0b72c2"/></svg>Tulsa : 555-019-0030</li>
      <li><svg width="14" height="14" viewBox="0 0 24 24"><path d="M5 3c2-1 3 0 4 3s0 3-1 4c1 3 3 5 6 6 1-1 1-2 4-1s4 2 3 4c-3 3-7 2-11-2S2 6 5 3z" fill="#0b72c2"/></svg>Oklahoma City : 555-017-9009</li>
    </ul>
  </div>
  <div class="footer-col newsletter abs" style="left:428px">
    <h4>NEWSLETTER SIGN UP</h4>
    <p>Lorem ipsum is the simple dummy text of print of type.</p>
    <div class="field">User Name *</div>
    <div class="field">Email Id *</div>
    <div class="btn-sub">SUBSCRIBE</div>
  </div>
  <div class="footer-brand abs"><span class="brand-dot"></span>Corvane IT</div>
  <div class="social abs" aria-label="Social links"><span></span><span></span><span></span></div>
</footer>

<div class="copyright abs">©Corvane IT- 2017 All Right Reserved</div>

</body>
</html>
```